Popup Nightclub Grand Opening Flyer

We need to design a flyer for the grand opening of an upscale, exclusive nightclub called "Lantern". The design needs to be chic and exclusive. The background should be black and the text should primarily be white. We like minimalist designs.

Here is the text for the flyer
-
Velvetroll Atlanta Presents

Lantern (LOGO)

A Popup Nightclub Experience
For one night Only

Friday, October 18, 2013
Party begins at 9PM

INVITE ONLY

See invitation for location details
(Velvetroll Atlanta logo)

-
Examples we like

http://cdn4-x.pressfolio-example.com/sites/default/files/styles/image_content_width/hash/3b/fd/2468013579_4421_flyer.jpg?itok=K9rtQw2z

http://files.hubspace-example.net/files/8Hqq-Tr72WWE3kaRbTmcxP5QZK2F396J8nbRw4CKMHfdX2Y7qSEF-MqjxDoNrLY3QCyQJD7npjGaRq3k-Mhx6hqf3MDSWf8r3/2zenSaturdays.jpg

http://morvex-example.com/wp-content/uploads/siteskin/widgetkit/gallery/2zen/2zen-gen_qstay4-01.jpg

Hi All, one thing that we are seeing that we don't like is on over emphasis on the phrase "a popup nightclub experience" please don't make this the largest thing on the flyer

Target Market(s)

Target market is 25-35 year olds who are affluent (rich) and like luxury brands

Requirements
Must have
• Dark Background
Nice to have
• Velvetroll Logo on the bottom
Modern text that isn't curvy
Should not have
• Curved text

```html
<!DOCTYPE html>
<html lang="en">
<head>
<meta charset="utf-8">
<title>Velvetroll Atlanta Presents – Lantern Nightclub</title>
<link rel="stylesheet" href="https://fonts.googleapis.com/css2?family=Marcellus&family=Poiret+One&family=Josefin+Sans:wght@300&display=swap">
<style>
  :root {
    --bg: #000000;
    --white: #ffffff;
    --silver-light: #e2e2e2;
    --silver-dark: #8a8a8a;
    --aqua-line: #9fd2d6;
    --aqua-fill: #07191b;
    --grey-line: #c9c9c9;
    --grey-fill: #151515;
    --invite-grey: #b8b8b8;
  }
  html, body {
    margin: 0;
    padding: 0;
    background: var(--bg);
    overflow: hidden;
  }
  .flyer {
    position: relative;
    width: 928px;
    height: 1200px;
    background: var(--bg);
    overflow: hidden;
    font-family: "Marcellus", serif;
  }
  .flyer > * { position: absolute; margin: 0; line-height: 1; }

  .presenter {
    top: 4px; left: 0; width: 100%;
    text-align: center;
    font-weight: 400;
    font-size: 62px;
    letter-spacing: 3px;
    background: linear-gradient(180deg, var(--silver-light), var(--silver-dark));
    -webkit-background-clip: text;
    background-clip: text;
    color: transparent;
  }
  .tagline {
    left: 0; width: 100%;
    text-align: center;
    color: var(--white);
    font-size: 42px;
    letter-spacing: 1px;
  }
  .tagline--first { top: 84px; }
  .tagline--second { top: 172px; }

  .event-date {
    top: 230px; left: 0; width: 100%;
    text-align: center;
    font-family: "Poiret One", sans-serif;
    font-weight: 400;
    font-size: 84px;
    letter-spacing: 1px;
    color: var(--aqua-fill);
    -webkit-text-stroke: 1.6px var(--aqua-line);
    white-space: nowrap;
  }

  .start-time {
    top: 405px; left: 0; width: 100%;
    text-align: center;
    font-family: "Poiret One", sans-serif;
    font-size: 64px;
    letter-spacing: 4px;
    color: var(--aqua-fill);
    -webkit-text-stroke: 1.6px var(--aqua-line);
    white-space: nowrap;
  }

  .venue-mark {
    top: 510px; left: 359px;
    width: 210px; height: 210px;
  }

  .venue-name, .venue-type {
    left: 0; width: 100%;
    text-align: center;
    font-family: "Josefin Sans", sans-serif;
    font-weight: 300;
    color: var(--white);
  }
  .venue-name {
    top: 798px;
    font-size: 108px;
    letter-spacing: 14px;
    text-indent: 14px;
  }
  .venue-type {
    top: 930px;
    font-size: 62px;
    letter-spacing: 6px;
    text-indent: 6px;
  }

  .access {
    top: 1012px; left: 0; width: 100%;
    text-align: center;
    font-size: 56px;
    color: var(--invite-grey);
  }

  .location-note {
    top: 1118px; left: 10px;
    font-family: "Poiret One", sans-serif;
    font-size: 42px;
    letter-spacing: 1px;
    color: var(--grey-fill);
    -webkit-text-stroke: 1.4px var(--grey-line);
    white-space: nowrap;
  }
  .presenter-sign {
    top: 1130px; left: 782px;
    font-family: "Josefin Sans", sans-serif;
    font-weight: 300;
    font-size: 18px;
    letter-spacing: 1px;
    color: var(--white);
    white-space: nowrap;
  }
</style>
</head>
<body>
<main class="flyer">
  <h2 class="presenter">Velvetroll Atlanta Presents</h2>
  <p class="tagline tagline--first">A Popup Nightclub experience</p>
  <p class="tagline tagline--second">for one night only</p>

  <h1 class="event-date">FRIDAY, OCTOBER 18, 2013</h1>

  <p class="start-time">PARTY BEGINS AT 9PM</p>

  <svg class="venue-mark" viewBox="0 0 210 210" aria-hidden="true">
    <circle cx="105" cy="105" r="100" fill="none" stroke="#cfcfcf" stroke-width="6"/>
  </svg>

  <p class="venue-name">LANTERN</p>
  <p class="venue-type">NIGHTCLUB</p>

  <p class="access">invite only</p>

  <p class="location-note">SEE INVITATION FOR LOCATION DETAILS</p>
  <p class="presenter-sign">VELVETROLL</p>
</main>
</body>
</html>
```